Criação de Papelaria (6 itens) para Viagens & Lazer
A empresa queria:
" A Corvelo Viagens é uma marca Institucional que tem como propósito a realização de sonhos em todas as esferas do Negocio. "

```html
<!DOCTYPE html>
<html lang="pt-BR">
<head>
<meta charset="utf-8">
<title>Corvelo Viagens – Papelaria Egito</title>
<link rel="stylesheet" href="https://fonts.googleapis.com/css2?family=Montserrat:wght@400;500;600;700&display=swap">
<style>
:root{
  --grey:#7a7d80;
  --grey-dark:#55595d;
  --grey-light:#9a9da0;
  --yellow:#e9b400;
  --wine:#a8322d;
  --line:#dcdcdc;
  --rainbow:linear-gradient(90deg,#f39200 0%,#e5007d 12%,#7b2e8e 24%,#2d3e9c 36%,#009fe3 48%,#3aaa35 60%,#ffd500 72%,#e30613 84%,#f39200 100%);
}
*{margin:0;padding:0;box-sizing:border-box}
html,body{width:1200px;height:1200px;overflow:hidden;background:#fff}
body{position:relative;font-family:"Montserrat",Arial,sans-serif;color:var(--grey)}

.band{position:absolute;left:0;width:100%;background:var(--rainbow)}

/* Email signature */
.signature{position:absolute;left:67px;top:151px;width:1073px;height:245px;background:#fff;border:1px solid var(--line);overflow:hidden}
.signature .band{height:17px}
.signature .band.top{top:0}
.signature .band.bottom{bottom:0}
.photo{position:absolute}
.photo.pyramids{left:0;top:17px;width:240px;height:106px;background:linear-gradient(180deg,#e7852e 0%,#f0a552 55%,#9a5a25 100%)}
.photo.sphinx{left:0;top:123px;width:240px;height:105px;background:linear-gradient(180deg,#7fb3e0 0%,#b9cfe0 45%,#c99a5e 70%,#a8733c 100%)}
.photo.temple{left:552px;top:17px;width:250px;height:211px;background:linear-gradient(135deg,#5a3a1c 0%,#b98a4e 40%,#d8b47a 60%,#8a6234 100%)}
.signature .brand{position:absolute;left:240px;top:17px;width:312px;height:211px;display:flex;align-items:center;justify-content:center}
.sig-contact{position:absolute;left:802px;top:17px;width:271px;height:211px;padding:38px 0 0 22px}
.sig-contact .item{display:flex;gap:10px;margin-bottom:14px}
.sig-contact p{font-size:18px;line-height:22px;color:var(--grey);text-transform:uppercase;letter-spacing:.3px;white-space:nowrap}

.brand-name{display:flex;align-items:center;gap:10px;white-space:nowrap}
.brand-name .mark{flex:none;width:12px;height:12px;background:var(--yellow)}
.brand-name span{font-weight:500;color:var(--grey);line-height:1}
.signature .brand-name span{font-size:34px}

.icon{flex:none;width:26px;height:26px}

/* Letterhead strip */
.letterhead{position:absolute;left:67px;top:444px;width:1073px;height:619px;background:#fff}
.letterhead .band.top{top:0;height:31px}
.letterhead .band.bottom{bottom:0;height:31px}
.logo-panel{position:absolute;left:0;top:48px;width:100%;height:156px;background:linear-gradient(180deg,#e6e6e6 0%,#fff 12%,#fff 88%,#e6e6e6 100%);display:flex;align-items:center;justify-content:center}
.logo-panel .brand-name span{font-size:50px}
.site{position:absolute;top:230px;width:100%;text-align:center;font-size:21px;color:var(--yellow);letter-spacing:.5px}

.column{position:absolute;top:305px}
.column.agencies{left:58px}
.column.contact{left:448px}
.column.social{left:799px}
.column h2{font-size:27px;font-weight:700;color:var(--grey-dark);letter-spacing:.5px;margin-bottom:32px}
.column h2 span{font-weight:400;color:var(--grey)}

.agency{display:flex;gap:18px;margin-bottom:52px}
.flag{flex:none;width:73px;height:44px}
.agency h3{font-size:21px;font-weight:700;color:var(--wine);margin:2px 0 6px}
.agency p{font-size:11px;line-height:15px;color:var(--grey-light)}

.contact-item{display:flex;gap:14px;margin-bottom:22px}
.contact-item .icon{width:34px;height:34px}
.contact-item h3{font-size:20px;font-weight:700;color:var(--grey-dark);line-height:24px}
.contact-item p{font-size:19px;line-height:24px;color:var(--grey)}
.contact-item small{display:block;font-size:12px;line-height:16px;color:var(--grey-light)}

.social-item{display:flex;align-items:center;gap:14px;margin-bottom:30px}
.social-item .dot{width:34px;height:34px;border-radius:50%}
.social-item span{font-size:20px;color:var(--grey)}
</style>
</head>
<body>

<section class="signature">
  <div class="band top" role="img" aria-label="Faixa decorativa em mosaico multicolorido"></div>
  <div class="photo pyramids" role="img" aria-label="Foto das pirâmides de Gizé ao pôr do sol com camelo"></div>
  <div class="photo sphinx" role="img" aria-label="Foto da Esfinge com pirâmide ao fundo e céu azul"></div>
  <div class="brand">
    <div class="brand-name"><i class="mark"></i><span>Corvelo Egito</span></div>
  </div>
  <div class="photo temple" role="img" aria-label="Foto de sarcófago dourado e colunas de templo egípcio"></div>
  <div class="sig-contact">
    <div class="item">
      <svg class="icon" viewBox="0 0 26 26"><circle cx="13" cy="13" r="11.5" fill="none" stroke="var(--yellow)" stroke-width="2"/><path d="M9 7.5l2.2-.5 1.3 3-1.5 1.2a7 7 0 0 0 3.8 3.8l1.2-1.5 3 1.3-.5 2.2c-5.5.5-10-4-9.5-9.5z" fill="var(--yellow)"/></svg>
      <p>(011) 3417-8820<br>Grande São Paulo</p>
    </div>
    <div class="item">
      <svg class="icon" viewBox="0 0 26 26"><circle cx="13" cy="13" r="11.5" fill="none" stroke="var(--yellow)" stroke-width="2"/><path d="M9 7.5l2.2-.5 1.3 3-1.5 1.2a7 7 0 0 0 3.8 3.8l1.2-1.5 3 1.3-.5 2.2c-5.5.5-10-4-9.5-9.5z" fill="var(--yellow)"/></svg>
      <p>0800 725 1190<br>Grande São Paulo</p>
    </div>
  </div>
  <div class="band bottom" role="img" aria-label="Faixa decorativa em mosaico multicolorido"></div>
</section>

<section class="letterhead">
  <div class="band top" role="img" aria-label="Faixa decorativa em mosaico multicolorido"></div>
  <div class="logo-panel">
    <div class="brand-name"><i class="mark"></i><span>Corvelo Egito</span></div>
  </div>
  <p class="site">www.corvelo.com.br</p>

  <div class="column agencies">
    <h2>NOSSAS <span>AGÊNCIAS</span></h2>
    <div class="agency">
      <svg class="flag" viewBox="0 0 73 44" aria-label="Bandeira do Brasil" role="img"><rect width="73" height="44" fill="#1a9b3a"/><path d="M36.5 4 68 22 36.5 40 5 22z" fill="#ffd400"/><circle cx="36.5" cy="22" r="10" fill="#1d3f94"/></svg>
      <div>
        <h3>BRASIL</h3>
        <p>Rua das Acácias, 742 - Cj. 31<br>Paraíso - São Paulo - SP</p>
      </div>
    </div>
    <div class="agency">
      <svg class="flag" viewBox="0 0 73 44" aria-label="Bandeira do Peru" role="img"><rect width="73" height="44" fill="#fff"/><rect width="24" height="44" fill="#d7131c"/><rect x="49" width="24" height="44" fill="#d7131c"/></svg>
      <div>
        <h3>PERU</h3>
        <p>Calle Los Olivos, 118<br>Centro Histórico de Cusco</p>
      </div>
    </div>
  </div>

  <div class="column contact">
    <h2>FALE <span>CONOSCO</span></h2>
    <div class="contact-item">
      <svg class="icon" viewBox="0 0 26 26"><circle cx="13" cy="13" r="11.5" fill="none" stroke="var(--yellow)" stroke-width="2"/><path d="M9 7.5l2.2-.5 1.3 3-1.5 1.2a7 7 0 0 0 3.8 3.8l1.2-1.5 3 1.3-.5 2.2c-5.5.5-10-4-9.5-9.5z" fill="var(--yellow)"/></svg>
      <div>
        <h3>Grande São Paulo</h3>
        <p>+55 (11) 3417-8820</p>
        <h3>Demais Regiões</h3>
        <p>0800 725 1190</p>
      </div>
    </div>
    <div class="contact-item">
      <svg class="icon" viewBox="0 0 26 26"><circle cx="13" cy="13" r="11.5" fill="none" stroke="var(--yellow)" stroke-width="2"/><rect x="7.5" y="8.5" width="11" height="7.5" rx="1.5" fill="none" stroke="var(--yellow)" stroke-width="1.6"/><path d="M10 16v3l3-3" fill="none" stroke="var(--yellow)" stroke-width="1.6"/></svg>
      <div>
        <h3>Mensageiro</h3>
        <small>Somente Orçamentos</small>
        <p>(11) 9721-5408</p>
      </div>
    </div>
  </div>

  <div class="column social">
    <h2>SIGA-<span>NOS</span></h2>
    <div class="social-item"><i class="dot" style="background:#3b5a8f"></i><span>facelink</span></div>
    <div class="social-item"><i class="dot" style="background:#3aa4d8"></i><span>chirper</span></div>
    <div class="social-item"><i class="dot" style="background:#a8322d"></i><span>circles+</span></div>
  </div>

  <div class="band bottom" role="img" aria-label="Faixa decorativa em mosaico multicolorido"></div>
</section>

</body>
</html>
```